TWPC Business Card Design

Business card for sole operator professional civil and traffic engineer.
Clients are developers and planners who require assistance with traffic strategic master planning advice and design development for access and infrastructure associated with the development.
Colours already in use are greens for the business name and black for other legend. The attached file shows the letterhead template which is currently in use.
Target Market(s)
Professional Clients in development industry
Most clients known to the Principal and card is mostly required to allow ongoing contact
Industry/Entity Type
Business
Contact Information for Business Card
LACHLAN PETTIGREW CONSULTING PARTNERS
ABN 37 814 529 106
PO Box 418 KELWOOD NSW 2619
Lachlan Pettigrew 0412 358 971
l.pettigrew@corvanmail.net

```html
<!DOCTYPE html>
<html lang="en">
<head>
<meta charset="utf-8">
<title>Lachlan Pettigrew Consulting Partners – Business Card</title>
<link rel="stylesheet" href="https://fonts.googleapis.com/css2?family=Roboto:wght@300;400&display=swap">
<style>
  :root {
    --backdrop: #5a3324;
    --card: #000000;
    --green: #8cc43c;
    --divider: #d9d9d9;
  }
  * { margin: 0; padding: 0; box-sizing: border-box; }
  html, body {
    width: 1200px;
    height: 960px;
    overflow: hidden;
    background: var(--backdrop);
    font-family: "Roboto", Arial, sans-serif;
  }
  .card {
    position: absolute;
    left: 120px;
    top: 188px;
    width: 960px;
    height: 584px;
    background: var(--card);
    border-radius: 34px;
    color: var(--green);
    font-weight: 300;
  }
  .divider {
    position: absolute;
    left: 480px;
    top: 96px;
    width: 2px;
    height: 440px;
    background: linear-gradient(to bottom, rgba(217,217,217,0), var(--divider) 50%, rgba(217,217,217,0.15));
  }
  .company {
    position: absolute;
    left: 62px;
    bottom: 92px;
    line-height: 1.08;
  }
  .company-name {
    font-size: 34px;
    letter-spacing: -0.5px;
    text-transform: uppercase;
  }
  .company-abn {
    margin-top: 10px;
    font-size: 22px;
  }
  .principal {
    position: absolute;
    right: 120px;
    top: 76px;
    font-size: 30px;
    letter-spacing: -0.3px;
  }
  .contact {
    position: absolute;
    right: 56px;
    bottom: 96px;
    list-style: none;
    font-size: 20px;
    line-height: 1.35;
  }
  .contact li {
    display: flex;
    justify-content: flex-end;
    align-items: center;
    gap: 14px;
  }
  .contact svg {
    width: 15px;
    height: 15px;
    fill: var(--green);
    flex: none;
  }
</style>
</head>
<body>
  <div class="card">
    <div class="company">
      <p class="company-name">Lachlan Pettigrew<br>Consulting Partners</p>
      <p class="company-abn">ABN 37 814 529 106</p>
    </div>

    <div class="divider"></div>

    <p class="principal">Lachlan Pettigrew</p>

    <ul class="contact">
      <li>0412 358 971
        <svg viewBox="0 0 16 16" aria-hidden="true"><path d="M1 5c0-2 1.5-3 7-3s7 1 7 3v1.5h-3.5V5H4.5v1.5H1zM3 8l2-2h6l2 2v6H3z"/></svg>
      </li>
      <li>PO Box 418 KELWOOD NSW 2619
        <svg viewBox="0 0 16 16" aria-hidden="true"><path d="M8 1a5 5 0 0 1 5 5c0 4-5 9-5 9S3 10 3 6a5 5 0 0 1 5-5zm0 3a2 2 0 1 0 0 4 2 2 0 0 0 0-4z"/></svg>
      </li>
      <li>l.pettigrew@corvanmail.net
        <svg viewBox="0 0 16 16" aria-hidden="true"><path d="M1 3h14v10H1zm1.5 1.5L8 9l5.5-4.5z"/></svg>
      </li>
    </ul>
  </div>
</body>
</html>
```